Sparrow Haulage needs a business card design.

Design a double-sided business card for new freight business. On the front, would like to see our logo along with the following info:

Martin Obuya
CEO/FOUNDER
555-206-7142
martinobuya@sparrow-haulage.example

On the reverse side, we would like to use the graphic image of our logo only without the Sparrow Haulage name.

```html
<!DOCTYPE html>
<html lang="en">
<head>
<meta charset="utf-8">
<title>Sparrow Haulage – Business Card</title>
<link href="https://fonts.googleapis.com/css2?family=Arimo:wght@400;700&display=swap" rel="stylesheet">
<style>
  :root {
    --page-bg: #000000;
    --card-bg: #2e2f33;
    --ink: #ffffff;
    --ink-soft: #e9e9ec;
    --rule: #55565c;
    --brand-red: #b50d0d;
    --brand-navy: #0a0f6b;
  }
  * { box-sizing: border-box; margin: 0; padding: 0; }
  html, body {
    width: 1200px; height: 900px; overflow: hidden;
    background: var(--page-bg);
    font-family: "Arimo", Arial, sans-serif;
  }
  .sheet { position: relative; width: 1200px; height: 900px; }
  .card {
    position: absolute; top: 266px;
    width: 458px; height: 282px;
    background: var(--card-bg);
    border-radius: 13px;
  }
  .card--front { left: 138px; }
  .card--back { left: 625px; }

  .brand {
    position: absolute; left: 20px; top: 121px;
    display: flex; align-items: center; gap: 9px;
  }
  .brand__square { width: 14px; height: 14px; background: var(--ink); }
  .brand__name {
    color: var(--ink); font-weight: 700; font-size: 15px;
    letter-spacing: 0.14em; line-height: 15px; text-transform: uppercase;
  }
  .divider {
    position: absolute; left: 192px; top: 86px;
    width: 1px; height: 108px; background: var(--rule);
  }
  .person { position: absolute; left: 205px; top: 86px; color: var(--ink); }
  .person__name { font-weight: 700; font-size: 18px; line-height: 20px; text-transform: uppercase; }
  .person__role { font-size: 13.5px; line-height: 16px; color: var(--ink-soft); margin-top: 1px; }
  .contacts { list-style: none; margin-top: 20px; }
  .contacts__item {
    display: flex; align-items: center; gap: 6px;
    font-size: 12px; line-height: 17px; color: var(--ink);
    white-space: nowrap;
  }
  .contacts__icon { width: 12px; height: 12px; flex: none; }

  .back-mark {
    position: absolute; left: 161px; top: 74px;
    width: 135px; height: 135px;
    background: linear-gradient(90deg, var(--brand-navy) 0%, var(--brand-navy) 35%, var(--brand-red) 65%, var(--brand-red) 100%);
  }
</style>
</head>
<body>
<main class="sheet">
  <section class="card card--front" aria-label="Business card front">
    <div class="brand">
      <span class="brand__square"></span>
      <span class="brand__name">Sparrow<br>Haulage</span>
    </div>
    <div class="divider"></div>
    <div class="person">
      <h1 class="person__name">Martin Obuya</h1>
      <p class="person__role">CEO/FOUNDER</p>
      <ul class="contacts">
        <li class="contacts__item">
          <svg class="contacts__icon" viewBox="0 0 12 12" aria-hidden="true"><path d="M2.5 1 L4.3 2.8 L3.4 4.3 Q4.6 6.9 7.7 8.6 L9.2 7.7 L11 9.5 L9.6 11 Q5.5 10.6 2.6 7.5 Q0.6 5 1 2.4 Z" fill="none" stroke="#fff" stroke-width="1.2"/></svg>
          <span>555-206-7142</span>
        </li>
        <li class="contacts__item">
          <svg class="contacts__icon" viewBox="0 0 12 12" aria-hidden="true"><rect x="0.5" y="2.5" width="11" height="7.5" fill="#fff"/><path d="M0.5 2.5 L6 7 L11.5 2.5" fill="none" stroke="#2e2f33" stroke-width="1"/></svg>
          <span>martinobuya@sparrow-haulage.example</span>
        </li>
        <li class="contacts__item">
          <svg class="contacts__icon" viewBox="0 0 12 12" aria-hidden="true"><g fill="none" stroke="#fff" stroke-width="1"><circle cx="6" cy="6" r="5.2"/><ellipse cx="6" cy="6" rx="2.3" ry="5.2"/><path d="M0.8 6 H11.2 M1.6 3.4 H10.4 M1.6 8.6 H10.4"/></g></svg>
          <span>www.sparrow-haulage.example</span>
        </li>
      </ul>
    </div>
  </section>

  <section class="card card--back" aria-label="Business card back">
    <div class="back-mark" role="img" aria-label="Sparrow Haulage logo symbol in navy and red"></div>
  </section>
</main>
</body>
</html>
```